Podiatry clinic requires a modern revamp and editing of existing website.

I would like a fresh new look and updated information for my current business website. An easy to navigate site with prominent address and phone number for call to action. We are a podiatry clinic that focuses on general and sports podiatry.
I would like 4 pages; including Home page, About Us, Services & Contact.
www.brambleridgepodiatry.net

Target Market(s)

Active working professionals.

Industry/Entity Type

Medical

Coding

Coded - Design and coding required

Number of Pages Required

4 page

Font styles to use
Sans Serif

Colors
6b449b

Requirements
Must have
• A modern look with logo and active images; clean and uncluttered. Visible phone number and address for call to action.
• 4 pages - Home, About Us, Services, Contact.
• Home page - update address & service logos.
• About Us - update of personal information.
• Services - Revamp of existing page.
• Contact page to include Google map, email & phone number.
Nice to have
• Ability to add content easily; eg. a blog or adding video onto Home page.
• Link to Facebook page.

```html
<!DOCTYPE html>
<html lang="en">
<head>
<meta charset="utf-8">
<title>Bramble Ridge Podiatry</title>
<link rel="stylesheet" href="https://fonts.googleapis.com/css2?family=Open+Sans:wght@400;600;700&family=Roboto+Condensed:wght@400;700&family=Arimo:wght@400;700&display=swap">
<style>
:root{
  --purple:#4b2a8f;
  --violet:#6b449b;
  --lilac:#8a6cc8;
  --orange:#f07d1a;
  --ink:#333;
  --line:#cfcfd6;
  --grey-bg:#e6e6e6;
  --panel:#ececec;
}
*{box-sizing:border-box;margin:0;padding:0}
html,body{width:1200px;height:2786px;overflow:hidden}
body{background:var(--grey-bg);font-family:"Open Sans",Arial,sans-serif;color:var(--ink);position:relative}
.page{position:absolute;left:15px;top:15px;width:1170px;height:2757px;background:#fff;overflow:hidden}
.abs{position:absolute}

/* header */
.brand{left:30px;top:40px;display:flex;align-items:center;gap:14px}
.brand-dot{width:56px;height:56px;border-radius:50%;background:var(--violet)}
.brand-name{font-size:30px;font-weight:700;color:var(--violet);line-height:1.05;width:200px}
.enquiry{left:639px;top:47px;font-size:19px;font-weight:700;color:var(--purple)}
.contact-row{left:636px;top:82px;display:flex;gap:36px;font-size:18px;font-weight:700;color:#222;align-items:center}
.contact-row span{display:flex;align-items:center;gap:10px}

/* nav */
.nav{left:0;top:167px;width:1170px;height:45px;background:var(--purple)}
.nav a{position:absolute;top:0;height:45px;line-height:45px;font-family:"Roboto Condensed",Arial,sans-serif;font-weight:700;font-size:15px;color:#fff;text-decoration:none;text-align:center;white-space:nowrap}
.nav a.active{background:var(--orange)}

/* hero */
.hero{left:0;top:212px;width:1170px;height:503px;display:flex}
.hero div{flex:1}
.hero .p1{background:linear-gradient(160deg,#6d7383,#c98a4b 55%,#2d3038)}
.hero .p2{background:linear-gradient(180deg,#3a3a40,#6e7a86 55%,#8a96a0)}
.hero .p3{background:linear-gradient(180deg,#d7c077,#8f7a5a 55%,#3a3a3e)}
.hero .p4{background:linear-gradient(180deg,#4a3a34,#b5755a 55%,#5a3e34)}

/* intro */
.intro{left:0;top:715px;width:1170px;height:301px;background:var(--purple);color:#fff;text-align:center;padding:35px 60px 0}
.intro p{font-size:18px;line-height:1.45;margin-bottom:24px}
.btn{position:absolute;top:212px;height:48px;width:331px;border-radius:8px;font-family:"Roboto Condensed",Arial,sans-serif;font-size:21px;line-height:44px;text-align:center;border:2px solid #fff}
.btn-learn{left:245px;background:var(--lilac);color:#fff}
.btn-book{left:594px;background:#fff;color:var(--purple);border-color:#3b7fc4}

/* services */
.services{left:0;top:1016px;width:1170px;height:570px}
.section-title{position:absolute;left:0;width:100%;text-align:center;font-size:26px;font-weight:700;color:#222}
.services svg text{font-family:"Open Sans",Arial,sans-serif;font-size:14px;font-weight:600;fill:#333}

/* blog */
.blog{left:0;top:1586px;width:1170px;height:539px;background:linear-gradient(180deg,#4f3391,#6a4da8 60%,#5a3f9a)}
.blog .section-title{color:#fff;top:64px}
.card{position:absolute;top:166px;width:267px;height:329px;background:#fff;border-radius:4px;padding:6px}
.card-inner{height:100%;background:linear-gradient(180deg,#f3f3f3,#dedede);position:relative}
.card-img{height:172px}
.card h3{font-family:"Arimo",Arial,sans-serif;font-size:14px;font-weight:700;margin:9px 12px 2px;color:#222}
.card p{font-family:"Arimo",Arial,sans-serif;font-size:14px;line-height:1.25;margin:0 12px;color:#333}
.card .more{position:absolute;left:50%;bottom:14px;transform:translateX(-50%);width:180px;height:42px;border-radius:4px;background:var(--purple);color:#fff;font-family:"Roboto Condensed",Arial,sans-serif;font-weight:700;font-size:17px;line-height:42px;text-align:center}

/* partners */
.partners{left:0;top:2125px;width:1170px;height:290px}
.partners .section-title{top:65px}

/* contact */
.contact{left:0;top:2415px;width:1170px;height:301px;background:var(--panel)}
.map{position:absolute;left:0;top:0;width:650px;height:301px;background:linear-gradient(135deg,#efe8d6,#f5efdf 40%,#e8dcc0 70%,#f1e6cc)}
.address{position:absolute;left:788px;top:50px;font-size:16px;font-weight:600;color:#222;line-height:24px}
.address .row{display:flex;gap:12px;margin-bottom:22px}
.social{display:flex;gap:6px;margin-left:24px}
.social i{display:block;width:19px;height:19px;border-radius:50%;background:var(--purple)}

/* footer */
.footer{left:0;top:2716px;width:1170px;height:41px;background:var(--purple);color:#fff;font-size:11px;font-weight:700;line-height:41px;padding:0 27px;display:flex;justify-content:space-between}
</style>
</head>
<body>
<div class="page">

  <header>
    <div class="abs brand"><span class="brand-dot"></span><span class="brand-name">Bramble Ridge Podiatry</span></div>
    <div class="abs enquiry">For Appointments or Enquiries</div>
    <div class="abs contact-row">
      <span>
        <svg width="28" height="28" viewBox="0 0 28 28"><circle cx="14" cy="14" r="12.5" fill="none" stroke="#f07d1a" stroke-width="2"/><path d="M10 8l3 3-2 2c1 2 2 3 4 4l2-2 3 3-2 2c-5 0-10-5-10-10z" fill="#f07d1a"/></svg>
        1300 555 014
      </span>
      <span>
        <svg width="28" height="28" viewBox="0 0 28 28"><circle cx="14" cy="14" r="12.5" fill="none" stroke="#f07d1a" stroke-width="2"/><rect x="8" y="10" width="12" height="9" fill="#f07d1a"/><path d="M8 10l6 5 6-5" fill="none" stroke="#fff" stroke-width="1.3"/></svg>
        info@brambleridgepodiatry.net
      </span>
    </div>
  </header>

  <nav class="abs nav">
    <a class="active" style="left:318px;width:91px">HOME</a>
    <a style="left:418px;width:70px">ABOUT</a>
    <a style="left:514px;width:110px">OUR SERVICES</a>
    <a style="left:617px;width:100px">CONTACT US</a>
    <a style="left:785px;width:50px">BLOG</a>
  </nav>

  <section class="abs hero">
    <div class="p1" role="img" aria-label="Photo of a runner's foot with highlighted heel"></div>
    <div class="p2" role="img" aria-label="Photo of runners' legs on a road"></div>
    <div class="p3" role="img" aria-label="Photo of a runner at sunset"></div>
    <div class="p4" role="img" aria-label="Photo of a running shoe on a track"></div>
  </section>

  <section class="abs intro">
    <p>Bramble Ridge Podiatry is a Podiatry clinic in the heart of Fernvale town centre. We are located between Alder &amp; Rowan Streets in the Harbourside Business Centre / Linden Hotel Complex. Our podiatrists are fully qualified health professionals who are able to diagnose, treat, manage or help to prevent all medical conditions that affect the feet and lower limb.</p>
    <p>We provide General Podiatry Treatment and some Specialised Services in relation to various foot conditions, including Sports Injuries, Orthotic Therapy and Nail Surgery.</p>
    <div class="btn btn-learn">LEARN MORE ABOUT US</div>
    <div class="btn btn-book">BOOK AN APPOINTMENT</div>
  </section>

  <section class="abs services">
    <h2 class="section-title" style="top:60px">Our Podiatry Treatment Services</h2>
    <svg class="abs" style="left:0;top:0" width="1170" height="570" viewBox="0 0 1170 570">
      <g stroke="#cfcfd6" stroke-width="1.5">
        <line x1="414" y1="175" x2="560" y2="175"/>
        <line x1="264" y1="219" x2="540" y2="219"/>
        <line x1="414" y1="264" x2="540" y2="264"/>
        <line x1="264" y1="309" x2="540" y2="309"/>
        <line x1="414" y1="353" x2="540" y2="353"/>
        <line x1="264" y1="398" x2="540" y2="398"/>
        <line x1="414" y1="442" x2="540" y2="442"/>
        <line x1="264" y1="489" x2="560" y2="489"/>
        <line x1="630" y1="242" x2="756" y2="242"/>
        <line x1="630" y1="286" x2="907" y2="286"/>
        <line x1="630" y1="333" x2="756" y2="333"/>
        <line x1="630" y1="377" x2="907" y2="377"/>
        <line x1="630" y1="422" x2="756" y2="422"/>
      </g>
      <rect x="509" y="149" width="152" height="362" rx="76" fill="#4b2a8f" role="img" aria-label="Foot silhouette"/>
      <g fill="#fff" stroke="#4b2a8f" stroke-width="2">
        <circle cx="414" cy="175" r="20"/><circle cx="264" cy="219" r="20"/>
        <circle cx="414" cy="264" r="20"/><circle cx="264" cy="309" r="20"/>
        <circle cx="414" cy="353" r="20"/><circle cx="264" cy="398" r="20"/>
        <circle cx="414" cy="442" r="20"/><circle cx="264" cy="489" r="20"/>
        <circle cx="756" cy="242" r="20"/><circle cx="907" cy="286" r="20"/>
        <circle cx="756" cy="333" r="20"/><circle cx="907" cy="377" r="20"/>
        <circle cx="756" cy="422" r="20"/>
      </g>
      <g text-anchor="end">
        <text x="379" y="180">Nails</text>
        <text x="229" y="224">Corns</text>
        <text x="379" y="269">Callus</text>
        <text x="229" y="314">Warts</text>
        <text x="379" y="358">Skin Disorders</text>
        <text x="229" y="390">Heel Pain / Heel Spurs / Arch</text>
        <text x="229" y="408">Pain-Plantar Fasciitis,</text>
        <text x="379" y="437">Ankle Pain / Shin</text>
        <text x="379" y="455">Splints / Knee Pain</text>
        <text x="229" y="484">Bunions, Hammertoes and</text>
        <text x="229" y="502">Toe Deformities</text>
      </g>
      <text x="793" y="247">Diabetic Management</text>
      <text x="944" y="291">Nail Surgery</text>
      <text x="793" y="338">Biomechanical Assessment</text>
      <text x="944" y="382">Gait Analysis</text>
      <text x="793" y="427">Orthotic Therapy</text>
    </svg>
  </section>

  <section class="abs blog" aria-label="Latest blog">
    <h2 class="section-title">Latest Blog</h2>
    <article class="card" style="left:30px"><div class="card-inner">
      <div class="card-img" role="img" aria-label="X-ray style image of a foot with heel pain" style="background:linear-gradient(135deg,#1c1c1c,#6a6a6a 55%,#c4662a)"></div>
      <h3>News #1</h3><p>Lorem ipsum dolor sit amet, consec tetuer adipiscing elit, sed diam.</p>
      <div class="more">READ MORE</div></div></article>
    <article class="card" style="left:311px"><div class="card-inner">
      <div class="card-img" role="img" aria-label="Blue jigsaw puzzle pieces" style="background:linear-gradient(135deg,#0f3446,#3a8aa8 55%,#0d2a38)"></div>
      <h3>News #2</h3><p>Lorem ipsum dolor sit amet, consec tetuer adipiscing elit, sed diam.</p>
      <div class="more">READ MORE</div></div></article>
    <article class="card" style="left:592px"><div class="card-inner">
      <div class="card-img" role="img" aria-label="Running shoes on a road" style="background:linear-gradient(180deg,#6e6a63,#a59b8a 60%,#7a7368)"></div>
      <h3>News #3</h3><p>Lorem ipsum dolor sit amet, consec tetuer adipiscing elit, sed diam.</p>
      <div class="more">READ MORE</div></div></article>
    <article class="card" style="left:873px"><div class="card-inner">
      <div class="card-img" role="img" aria-label="Sprinter in starting position on a road" style="background:linear-gradient(180deg,#8a5a3a,#c98f5e 45%,#3e3a38)"></div>
      <h3>News #4</h3><p>Lorem ipsum dolor sit amet, consec tetuer adipiscing elit, sed diam.</p>
      <div class="more">READ MORE</div></div></article>
  </section>

  <section class="abs partners">
    <h2 class="section-title">Partners</h2>
    <svg class="abs" style="left:0;top:0" width="1170" height="290" viewBox="0 0 1170 290">
      <path d="M52 197l-10 10 10 10" fill="none" stroke="#444" stroke-width="3"/>
      <path d="M1118 197l10 10-10 10" fill="none" stroke="#444" stroke-width="3"/>
      <rect x="150" y="187" width="150" height="40" rx="4" fill="#2f2f2f" role="img" aria-label="Partner badge"/>
      <rect x="400" y="190" width="140" height="34" rx="3" fill="#1f9a4a" role="img" aria-label="Partner badge"/>
      <rect x="612" y="182" width="125" height="50" rx="6" fill="#2b4fa0" role="img" aria-label="Partner badge"/>
      <rect x="800" y="182" width="140" height="50" rx="6" fill="#1a4d8f" role="img" aria-label="Partner badge"/>
      <rect x="1000" y="177" width="56" height="60" rx="4" fill="#1f2c7a" role="img" aria-label="Partner badge"/>
    </svg>
  </section>

  <section class="abs contact">
    <div class="map" role="img" aria-label="Street map showing the clinic location"></div>
    <div class="address">
      <div class="row">
        <svg width="12" height="18" viewBox="0 0 12 18"><path d="M6 0a6 6 0 016 6c0 4-6 12-6 12S0 10 0 6a6 6 0 016-6z" fill="#4b2a8f"/><circle cx="6" cy="6" r="2.2" fill="#ececec"/></svg>
        <div>Bramble Ridge Podiatry<br>Suite 12<br>74 Larkspur Lane<br>Fernvale 3911</div>
      </div>
      <div class="row">
        <svg width="14" height="14" viewBox="0 0 14 14"><path d="M2 1l3 3-1.5 2c1 2 2.5 3.5 4.5 4.5L10 9l3 3-2 2C5.5 14 0 8.5 0 3z" fill="#4b2a8f"/></svg>
        <div>1300 555 014</div>
      </div>
      <div class="row">
        <svg width="14" height="14" viewBox="0 0 14 14"><rect x="0" y="3" width="14" height="9" fill="#4b2a8f"/><path d="M0 3l7 5 7-5" fill="none" stroke="#ececec" stroke-width="1.2"/></svg>
        <div>info@brambleridgepodiatry.net</div>
      </div>
      <div class="social"><i aria-label="Social link"></i><i aria-label="Social link"></i></div>
    </div>
  </section>

  <footer class="abs footer">
    <span>HOME &nbsp;|&nbsp; ABOUT US &nbsp;|&nbsp; OUR SERVICES &nbsp;|&nbsp; CONTACT US &nbsp;|&nbsp; BLOG</span>
    <span>COPYRIGHT © 2016 BRAMBLE RIDGE PODIATRY. ALL RIGHTS RESERVED.</span>
  </footer>

</div>
</body>
</html>
```